Business Card for Fashion House

We need a business card design for our personalize fashion service for our customers. the business card should reflect reliability, luxury and creativity.
The brand Gravetto is extracted from "Graceful Velvetto"; Gravetto provides fashion designs sprinkled with luxury and style tailored for our elite clients character profile.
Gravetto is created for those who embody class and elegance with a passion for style.
Target Market(s)
Affluent Customers
Industry/Entity Type
Fashion
Contact Information for Business Card
Samira Haddadin
Fashion Designer
Telephone: +971 4 555 0192
Mobile +971 50 555 0147
Emal info@gravetto-example.com
Website www.gravetto-example.com
Social Media Youtube g+ Facebook Instagram Pin /gravetto
Font styles to use
Other font styles liked:
- Audrey provided
Look and feel
Each slider illustrates characteristics of the customer's brand and the style your logo design should communicate.

```html
<!DOCTYPE html>
<html lang="en">
<head>
<meta charset="utf-8">
<title>Gravetto — Business Card</title>
<link rel="stylesheet" href="https://fonts.googleapis.com/css2?family=Marcellus&family=Roboto:wght@400&display=swap">
<style>
  :root {
    --backdrop: #3a3a3c;
    --card-black: #1d1d20;
    --silver-light: #f1f1f1;
    --silver-mid: #c9c9cb;
    --silver-dark: #9a9a9c;
    --ink: #141416;
    --name-white: #f4f4f4;
  }
  * { box-sizing: border-box; margin: 0; padding: 0; }
  html, body { width: 799px; height: 1200px; overflow: hidden; }
  body {
    background: var(--backdrop);
    display: flex;
    flex-direction: column;
    align-items: center;
    justify-content: center;
    gap: 150px;
  }
  .card {
    position: relative;
    width: 640px;
    height: 366px;
    background: var(--card-black);
    border-radius: 4px;
    overflow: hidden;
  }
  .brand-name {
    font-family: "Marcellus", serif;
    color: var(--silver-mid);
    letter-spacing: 0.42em;
    text-transform: uppercase;
  }
  .card--front .brand-name {
    position: absolute;
    left: 0; right: 0; top: 160px;
    text-align: center;
    font-size: 40px;
    padding-left: 0.42em;
  }
  .card--back .wave { position: absolute; inset: 0; }
  .card--back .brand-name {
    position: absolute;
    left: 40px; top: 70px;
    font-size: 26px;
  }
  .social-handle {
    position: absolute;
    left: 42px; top: 128px;
    display: flex; align-items: center; gap: 8px;
    font-family: "Roboto", sans-serif;
    font-size: 15px;
    color: var(--name-white);
  }
  .social-handle .dot {
    width: 12px; height: 12px; border-radius: 50%;
    background: var(--silver-mid);
  }
  .holder {
    position: absolute;
    right: 36px; top: 66px;
    text-align: right;
    color: var(--name-white);
  }
  .holder__name { font-family: "Marcellus", serif; font-size: 24px; }
  .holder__role { font-family: "Roboto", sans-serif; font-size: 13px; margin-top: 4px; color: #d8d8d8; }
  .contact {
    position: absolute;
    right: 36px; bottom: 26px;
    list-style: none;
    font-family: "Roboto", sans-serif;
    font-size: 15px;
    color: var(--ink);
  }
  .contact li {
    display: flex; justify-content: flex-end; align-items: center;
    gap: 10px; line-height: 22px;
  }
  .contact svg { width: 15px; height: 15px; fill: none; stroke: var(--ink); stroke-width: 1.6; }
</style>
</head>
<body>

  <section class="card card--front" aria-label="Card front">
    <div class="brand-name">Gravetto</div>
  </section>

  <section class="card card--back" aria-label="Card back">
    <svg class="wave" viewBox="0 0 640 366" preserveAspectRatio="none" aria-hidden="true">
      <defs>
        <linearGradient id="silver" x1="0" y1="0" x2="1" y2="0.3">
          <stop offset="0" stop-color="#b9b9bb"/>
          <stop offset="0.35" stop-color="#f4f4f4"/>
          <stop offset="0.65" stop-color="#cfcfd1"/>
          <stop offset="1" stop-color="#eeeeee"/>
        </linearGradient>
      </defs>
      <path d="M0,150 C120,130 210,215 350,222 C470,228 570,195 640,188 L640,366 L0,366 Z" fill="url(#silver)"/>
      <path d="M0,170 C130,150 220,232 350,240 C470,246 570,212 640,206" fill="none" stroke="var(--card-black)" stroke-width="9"/>
      <path d="M60,168 C150,170 230,248 350,254 C470,260 570,226 640,222" fill="none" stroke="var(--card-black)" stroke-width="4"/>
    </svg>

    <div class="brand-name">Gravetto</div>

    <div class="social-handle"><span class="dot"></span>/gravetto</div>

    <div class="holder">
      <div class="holder__name">Samira Haddadin</div>
      <div class="holder__role">Fashion Designer</div>
    </div>

    <ul class="contact">
      <li>+971 4 555 0192
        <svg viewBox="0 0 16 16" aria-hidden="true"><circle cx="8" cy="8" r="7"/><path d="M5.5 4.5l1.5 2-1 1c.6 1.2 1.3 1.9 2.5 2.5l1-1 2 1.5-1 1.5c-3 0-6-3-6-6z"/></svg>
      </li>
      <li>+971 50 555 0147
        <svg viewBox="0 0 16 16" aria-hidden="true"><rect x="4" y="1.5" width="8" height="13" rx="1.5"/><path d="M7 12.5h2"/></svg>
      </li>
      <li>info@gravetto-example.com
        <svg viewBox="0 0 16 16" aria-hidden="true"><rect x="1.5" y="3.5" width="13" height="9"/><path d="M1.5 3.5l6.5 5 6.5-5"/></svg>
      </li>
      <li>www.gravetto-example.com
        <svg viewBox="0 0 16 16" aria-hidden="true"><circle cx="8" cy="8" r="6.5"/><ellipse cx="8" cy="8" rx="2.8" ry="6.5"/><path d="M1.5 8h13"/></svg>
      </li>
    </ul>
  </section>

</body>
</html>
```